Hop Bright Meadow Business Website Branding

Looking for a wordpress template design with CSS and HTML encoding. Current website can be seen at hopbrightmeadow.example.

WE ARE CURRENTLY IN PROCESS GETTING A LOGO DESIGN... I HAVE INCLUDED THE TOP POTENTIAL DESIGNS FOR REFERENCE TO HELP UNDERSTAND WHAT STYLE WE ARE LOOKING FOR...
NOTE: THE “PEBBLE CREW” LOGO WAS A PREVIOUS COMPANY WE OWNED SO YOU CAN GE A FEEL FOR THE TYPE OF DESIGNS WE HAVE USED IN THE PAST.

My blog will focus on making a connection with wild Florida, it’s wildlife, plants and animals... with an eye toward Florida conservation, nature adventure trips, and education... Content, photos and other merchandise will also be offered for sale.
I’m looking for a site design that incorporates Florida nature and wildlife/plants, with a fun “Old Florida” retro-adventure feel.
When they see this site it should speak to the import of natural Florida and the critical nature of the ecosystem here... while being instantly recognizable and iconic... IE: when I think of florida I think of water, plants, warmth, sunsets etc...

https://join.chatroomhub.example/t/lumexstudio-kzt4821/shared_invite/zt-pqwrt83m-hRnLvXaKoPzsYcB1Uq7JdM

Target Market(s)

Nature, Education, Conservation, Photography

Industry/Entity Type

Photographer

Coding

Coded - Design and coding required

Requirements
Must have
• Need to have site wide template design which generally includes a landing page and a general page template for other pages... Must include html and css encoding...
Should not have
• Any animals included in the site should be Florida native... IE: no African animals etc... This will require some research to ensure that if animals are included that they are part of the Florida ecosystem.

```html
<!DOCTYPE html>
<html lang="en">
<head>
<meta charset="utf-8">
<title>Hop Bright Meadow</title>
<link rel="stylesheet" href="https://fonts.googleapis.com/css2?family=Kaushan+Script&family=Poppins:ital,wght@0,400;0,500;0,600;1,400;1,500&display=swap">
<style>
:root{
  --red:#b3261c;
  --red-dark:#8f1c14;
  --orange:#f08c1c;
  --parchment:#e9d4a9;
  --parchment-dark:#d9bd86;
  --ink:#2a2520;
  --navy:#101b31;
  --navy-2:#1b2a47;
  --white:#ffffff;
  --cream:#fbf6ec;
}
*{box-sizing:border-box;margin:0;padding:0}
html,body{width:1200px;height:3208px;overflow:hidden}
body{font-family:"Poppins",sans-serif;color:var(--ink);background:var(--parchment);position:relative}
.script{font-family:"Kaushan Script",cursive;font-weight:400}

/* header */
.site-header{position:absolute;top:0;left:0;width:1200px;height:150px;background:var(--cream);z-index:5}
.brand{position:absolute;left:56px;top:44px;display:flex;align-items:center;gap:14px}
.brand-dot{width:40px;height:40px;border-radius:50%;background:var(--orange)}
.brand-name{font-family:"Kaushan Script",cursive;font-size:40px;color:var(--red);line-height:1}
.call{position:absolute;right:70px;top:28px;display:flex;align-items:center;gap:12px}
.call-icon{width:46px;height:46px;border-radius:50%;background:var(--orange);display:flex;align-items:center;justify-content:center}
.call small{display:block;font-size:13px;color:#666}
.call strong{font-size:17px;font-weight:600;color:var(--ink)}
.main-nav{position:absolute;right:60px;top:100px;display:flex;gap:30px;font-size:14px;font-weight:500}
.main-nav a{color:var(--ink);text-decoration:none;padding-bottom:6px}
.main-nav a.active{color:var(--red);border-bottom:2px solid var(--red)}

/* hero */
.hero{position:absolute;top:150px;left:0;width:1200px;height:580px;background:linear-gradient(180deg,#8fb6d8 0%,#5e7f5a 45%,#3c5a2e 75%,#566b3a 100%);overflow:hidden}
.hero-inner{position:absolute;top:170px;left:0;width:100%;text-align:center;color:var(--white)}
.hero h1{font-size:68px;text-shadow:0 2px 8px rgba(0,0,0,.4)}
.hero p{width:520px;margin:14px auto 0;font-size:14px;line-height:1.6}
.btn{display:inline-block;background:var(--orange);color:var(--white);font-size:14px;font-weight:600;padding:12px 32px;border-radius:24px;text-decoration:none;letter-spacing:.5px}
.hero .btn{margin-top:26px}
.dots{position:absolute;bottom:64px;left:0;width:100%;display:flex;justify-content:center;gap:10px}
.dots span{width:14px;height:14px;border-radius:50%;border:2px solid var(--white)}
.dots span.on{background:var(--white)}
.wave{position:absolute;left:0;width:1200px;display:block}

/* welcome */
.welcome{position:absolute;top:730px;left:0;width:1200px;height:760px;text-align:center}
.section-title{font-size:64px;color:var(--ink)}
.welcome .section-title{margin-top:90px}
.welcome p{width:860px;margin:18px auto 0;font-size:14px;line-height:1.7}
.welcome .btn{margin-top:30px;padding:10px 28px;font-size:13px}
.moments{position:absolute;top:380px;left:0;width:1200px;height:300px}
.moment{position:absolute;width:250px;height:250px;border-radius:50%;border:6px solid var(--white);box-shadow:0 4px 12px rgba(0,0,0,.25)}
.m1{left:140px;top:20px;background:radial-gradient(circle,#8a8172 0%,#5c6a4c 70%)}
.m2{left:475px;top:20px;background:radial-gradient(circle,#d08a3c 0%,#6c5a3a 70%)}
.m3{left:810px;top:20px;background:radial-gradient(circle,#a58d6f 0%,#4f5d3f 70%)}

/* about */
.about{position:absolute;top:1470px;left:0;width:1200px;height:720px}
.about-band{position:absolute;inset:0}
.about-photo{position:absolute;left:150px;top:110px;width:420px;height:400px;border-radius:48% 52% 44% 56% / 52% 46% 54% 48%;background:linear-gradient(160deg,#7fb3d6 0%,#d9a27a 55%,#c0603e 100%);border:6px solid var(--white)}
.about-text{position:absolute;left:610px;top:130px;width:480px;color:var(--white)}
.about-text h2{font-size:62px;color:var(--white)}
.about-text p{margin-top:14px;font-size:13.5px;line-height:1.75}

/* testimonials */
.testimonials{position:absolute;top:2190px;left:0;width:1200px;height:580px;text-align:center}
.testimonials .section-title{margin-top:20px}
.quote-card{position:absolute;left:240px;top:120px;width:820px;height:190px;background:var(--white);border-radius:26px;box-shadow:0 6px 16px rgba(0,0,0,.18);padding:38px 60px}
.quote-card q{font-style:italic;font-size:21px;line-height:1.5;quotes:"\201C" "\201D"}
.quote-card cite{display:block;margin-top:16px;font-style:italic;font-weight:600;font-size:19px}
.arrow{position:absolute;top:195px;width:44px;height:44px;border-radius:50%;background:var(--red);display:flex;align-items:center;justify-content:center}
.arrow.prev{left:120px}
.arrow.next{right:120px}
.avatars{position:absolute;top:310px;left:0;width:100%;display:flex;justify-content:center;align-items:center;gap:18px}
.avatar{border-radius:50%;border:4px solid var(--white);box-shadow:0 3px 8px rgba(0,0,0,.25);background:linear-gradient(160deg,#9aa6b4,#4d5a6d)}
.avatar.sm{width:76px;height:76px}
.avatar.lg{width:112px;height:112px;background:linear-gradient(160deg,#8fb7d6,#3f5f82)}

/* footer */
.site-footer{position:absolute;top:2740px;left:0;width:1200px;height:468px;color:var(--white)}
.footer-bg{position:absolute;inset:0}
.footer-cols{position:absolute;top:130px;left:100px;width:1020px;display:flex}
.footer-cols h4{font-size:17px;font-weight:600;margin-bottom:22px}
.links{width:170px}
.links ul{list-style:none;font-size:13px;line-height:2.2}
.links li::before{content:"•";margin-right:10px;color:var(--orange)}
.contact{width:330px}
.contact-row{display:flex;align-items:center;gap:12px;font-size:13px;margin-bottom:16px}
.contact-row i{width:30px;height:30px;border-radius:50%;border:1.5px solid var(--white);display:flex;align-items:center;justify-content:center;flex:none}
.touch{width:500px}
.form-row{display:flex;gap:14px;margin-bottom:12px}
.field{flex:1;height:34px;background:var(--white);border-radius:3px;color:#888;font-size:12px;padding:9px 12px}
.field.area{height:72px}
.submit{float:right;background:var(--red);color:var(--white);font-size:12px;font-weight:600;padding:9px 22px;border-radius:3px;margin-top:2px}
.footer-bar{position:absolute;bottom:0;left:0;width:100%;height:52px;border-top:1px solid rgba(255,255,255,.2);display:flex;align-items:center;justify-content:space-between;padding:0 40px;font-size:12px}
.social{display:flex;gap:8px}
.social span{width:24px;height:24px;background:var(--red);border-radius:3px}
</style>
</head>
<body>

<header class="site-header">
  <div class="brand"><span class="brand-dot"></span><span class="brand-name">Hop Bright Meadow</span></div>
  <div class="call">
    <span class="call-icon"><svg width="22" height="22" viewBox="0 0 24 24"><path fill="#fff" d="M6.6 10.8a15.1 15.1 0 0 0 6.6 6.6l2.2-2.2c.3-.3.7-.4 1-.2 1.1.4 2.3.6 3.6.6.6 0 1 .4 1 1V20c0 .6-.4 1-1 1A17 17 0 0 1 3 4c0-.6.4-1 1-1h3.5c.6 0 1 .4 1 1 0 1.3.2 2.5.6 3.6.1.3 0 .7-.2 1z"/></svg></span>
    <div><small>Call us today:</small><strong>+1 555 014 2207</strong></div>
  </div>
  <nav class="main-nav">
    <a class="active" href="#">HOME</a><a href="#">ABOUT</a><a href="#">SERVICES</a><a href="#">BLOG</a><a href="#">FAQ</a><a href="#">CONTACT US</a>
  </nav>
</header>

<section class="hero">
  <div role="img" aria-label="Photo of a sunlit pine flatwoods forest with palmetto undergrowth" style="position:absolute;inset:0"></div>
  <div class="hero-inner">
    <h1 class="script">Hop Bright Meadow</h1>
    <p>Come wander through quiet pinelands, bright wetlands and open skies, and meet the wild places that make this state home.</p>
    <a class="btn" href="#">GET STARTED</a>
  </div>
  <div class="dots"><span class="on"></span><span></span><span></span></div>
  <svg class="wave" style="bottom:0" height="90" viewBox="0 0 1200 90" preserveAspectRatio="none">
    <path d="M0 70 C300 10 600 90 900 40 C1020 20 1120 20 1200 30 L1200 90 L0 90Z" fill="var(--orange)"/>
    <path d="M0 78 C300 20 600 96 900 50 C1020 30 1120 30 1200 40 L1200 90 L0 90Z" fill="var(--red)"/>
    <path d="M0 88 C300 34 600 104 900 62 C1020 44 1120 44 1200 52 L1200 90 L0 90Z" fill="var(--parchment)"/>
  </svg>
</section>

<section class="welcome">
  <h2 class="section-title script">Welcome</h2>
  <p>Come explore the wild side of the state with me as we discover native plants, quiet waters and the creatures that share them. Here you will find field notes, trip ideas and photo stories that celebrate the wetlands, pinelands and coasts, along with simple ways each of us can help protect these fragile places for future seasons.</p>
  <a class="btn" href="#">LEARN MORE</a>
  <div class="moments">
    <svg width="1200" height="300" viewBox="0 0 1200 300" style="position:absolute;left:0;top:0">
      <path d="M0 145 H1200" stroke="#1b1b1b" stroke-width="3" fill="none"/>
      <path d="M120 145 A145 145 0 0 0 410 145" stroke="#1b1b1b" stroke-width="4" fill="none"/>
      <path d="M455 145 A145 145 0 0 1 745 145" stroke="#1b1b1b" stroke-width="4" fill="none"/>
      <path d="M790 145 A145 145 0 0 0 1080 145" stroke="#1b1b1b" stroke-width="4" fill="none"/>
    </svg>
    <div class="moment m1" role="img" aria-label="Close-up photo of a small turtle held in an open hand"></div>
    <div class="moment m2" role="img" aria-label="Photo of an orange butterfly resting on wildflowers"></div>
    <div class="moment m3" role="img" aria-label="Photo of tall native grasses and seed heads"></div>
  </div>
</section>

<section class="about">
  <svg class="about-band" width="1200" height="720" viewBox="0 0 1200 720" preserveAspectRatio="none">
    <path d="M0 60 C250 0 450 90 700 40 C900 0 1080 20 1200 50 L1200 660 C950 720 700 640 450 690 C250 730 100 680 0 660Z" fill="var(--red)"/>
  </svg>
  <div class="about-photo" role="img" aria-label="Portrait photo of the site owner wearing sunglasses at the beach"></div>
  <div class="about-text">
    <h2 class="script">About Me</h2>
    <p>Hello Nature lovers! I'm Dana Fielding, a wildlife rescuer, Master Naturalist, nature writer and photographer. Busy mama of three kiddos, a colorful backyard flock, two very curious dogs and a garden that never sleeps. I have a passion for all things nature and I adore living in the Southwest. I will always be a wanderer at heart, but from the moment I set foot in this state my heart was home. For the past 20 years, I have been fortunate to have some very unique and special experiences caring for many different species of animals and educating the public about wildlife and the environment. My hope is that those I welcome in will better understand their connection with the natural world and our shared responsibility to protect the wild and precious lands.</p>
  </div>
</section>

<section class="testimonials">
  <h2 class="section-title script">Testimonials</h2>
  <div class="arrow prev"><svg width="16" height="16" viewBox="0 0 16 16"><path d="M10 3 L5 8 L10 13" stroke="#fff" stroke-width="2.5" fill="none"/></svg></div>
  <blockquote class="quote-card">
    <q>Nature has been for me, as long as I remember, a source of solace, inspiration, adventure, and delight; a home, a teacher, a companion.</q>
    <cite>Marisol Pennant</cite>
  </blockquote>
  <div class="arrow next"><svg width="16" height="16" viewBox="0 0 16 16"><path d="M6 3 L11 8 L6 13" stroke="#fff" stroke-width="2.5" fill="none"/></svg></div>
  <div class="avatars">
    <div class="avatar sm" role="img" aria-label="Reviewer portrait photo"></div>
    <div class="avatar lg" role="img" aria-label="Featured reviewer portrait photo"></div>
    <div class="avatar sm" role="img" aria-label="Reviewer portrait photo"></div>
  </div>
</section>

<footer class="site-footer">
  <svg class="footer-bg" width="1200" height="468" viewBox="0 0 1200 468" preserveAspectRatio="none">
    <defs><linearGradient id="night" x1="0" y1="0" x2="0" y2="1"><stop offset="0" stop-color="#1e3050"/><stop offset="1" stop-color="#0c1526"/></linearGradient></defs>
    <path d="M0 40 C300 0 650 70 900 30 C1050 8 1140 20 1200 30 L1200 468 L0 468Z" fill="var(--red)"/>
    <path d="M0 58 C300 18 650 88 900 48 C1050 26 1140 38 1200 48 L1200 468 L0 468Z" fill="url(#night)" role="img" aria-label="Night photo of a waterfront city skyline"/>
  </svg>
  <div class="footer-cols">
    <div class="links">
      <h4>Useful Links</h4>
      <ul><li>Home</li><li>About me</li><li>Service</li><li>Store</li><li>FAQ</li><li>Contact us</li></ul>
    </div>
    <div class="contact">
      <h4>Contact Information</h4>
      <div class="contact-row"><i><svg width="14" height="14" viewBox="0 0 24 24"><path fill="#fff" d="M12 2a7 7 0 0 0-7 7c0 5 7 13 7 13s7-8 7-13a7 7 0 0 0-7-7zm0 9.5A2.5 2.5 0 1 1 12 6.5a2.5 2.5 0 0 1 0 5z"/></svg></i><span>120 Cypress Hollow Road,<br>Suite 4, Marsh Point</span></div>
      <div class="contact-row"><i><svg width="14" height="14" viewBox="0 0 24 24"><path fill="#fff" d="M6.6 10.8a15.1 15.1 0 0 0 6.6 6.6l2.2-2.2c.3-.3.7-.4 1-.2 1.1.4 2.3.6 3.6.6.6 0 1 .4 1 1V20c0 .6-.4 1-1 1A17 17 0 0 1 3 4c0-.6.4-1 1-1h3.5c.6 0 1 .4 1 1 0 1.3.2 2.5.6 3.6.1.3 0 .7-.2 1z"/></svg></i><span>Phone: +1 555 014 2207</span></div>
      <div class="contact-row"><i><svg width="14" height="14" viewBox="0 0 24 24"><path fill="none" stroke="#fff" stroke-width="2" d="M3 6h18v12H3z M3 6l9 7 9-7"/></svg></i><span>Email: info@studioname.example</span></div>
      <div class="contact-row"><i><svg width="14" height="14" viewBox="0 0 24 24"><path fill="none" stroke="#fff" stroke-width="2" d="M6 9V3h12v6 M4 9h16v8H4z M7 14h10v7H7z"/></svg></i><span>Fax: 1 555 014 2208</span></div>
    </div>
    <div class="touch">
      <h4>Get In Touch</h4>
      <div class="form-row"><div class="field">Name</div><div class="field">Phone</div></div>
      <div class="form-row"><div class="field">Email</div></div>
      <div class="form-row"><div class="field area">Message</div></div>
      <div class="submit">SUBMIT</div>
    </div>
  </div>
  <div class="footer-bar">
    <span>Copyright © 2020, Company Name. All rights reserved | Privacy policy</span>
    <div class="social"><span></span><span></span><span></span></div>
  </div>
</footer>

</body>
</html>
```